WE ARE BRIGHT SPARROW, building a full website with ecommerce

requirements:
CODED FOR SITEQUILL
ONLINE STORE FUNCTION WITH E-COMMERCE USING TRADEBLOOM
PAGEWAVE AND PICTOLANE LINKS

I need a website design for my organization, WE ARE BRIGHT SPARROW, a global empowerment movement elevating woman, and the world. The site's home page should reflect our mission, to empower women. It should have a strong, empowering feel, with minimalistic design.
Please see www.lunavelto.com and http://www.corvenhal.co/ for an inspiration on layout and feel.

**PLEASE SEE ATTACHMENT "LOGO MOCK UP" FOR LOGO. THIS IS NOT THE FINAL VECTOR FILE, BUT THIS LOOKS THE SAME AS THE FINAL LOGO.

HOME PAGE:
The first section of the home page should include a background image with our logo center.

You should include the following links to pages at the top right of the page:
MISSION
MANTRA
ARMOR
MEET BS (I would like "bs" to be our logo)
pagewave and pictolane links

As you scroll down the page, you should see the following sections, which correlate to the links to pages as written above. **SEE ATTACHED SKETCH "HOMEPAGE LAYOUT IDEA" FOR REFERENCE**

WHO WE ARE (correlates to the link Mission)

OUR MANTRA (correlates to the link Mantra)

OUR ARMOR (correlates to the link The Shirt)
(This is where we will sell a shirt (and other apparel) and need the e-commerce function)

MEET BRIGHT SPARROWS (correlates to the link Meet BS)

SHOW OFF YOUR SUPER POWERS (correlates to the pagewave and pictolane)

FEATURED BRIGHT SPARROW (no link on top right of page)

On the homepage, for each of the above sections, as you scroll down there should be an image, either in the background or framed, next to the title (WHO WE ARE, for example), as well as one sentence of small text explaining the title. The title (WHO WE ARE) and the one sentence should link to a page (ie WHO WE ARE + the one sentence links to the MISSION page). ** SEE ATTACHED SKETCH "HOMEPAGE SECTION IDEAS" FOR REFERENCE**

**PLEASE SEE ATTACHMENT "WEBSITE TITLE IDEAS" FOR A STARTING PLACE OF THE LOOK. These don't have to be exact, but they give you an idea of what I'm looking for.

**FONTS TYPOLD EXTRA BOLD AND TYPOLD BOOK 500 (WHICH SHOULD BE BOLDED MANUALLY) ARE ATTACHED**

Target Market(s)

Women, mainly in US

Industry/Entity Type

Social

Coding

Coded - Design and coding required

Number of Pages Required

5+ page

Font styles to use
Other font styles liked:
• Typol Extra Bold

Requirements
Must have
• CODED FOR SITEQUILL
• ONLINE STORE FUNCTION WITH E-COMMERCE USING TRADEBLOOM
• PAGEWAVE AND PICTOLANE LINKS
• Typold Extra Bold and Typold Book 500, attached
• please see description for all requirements
Nice to have
• please see description for all ideas
Should not have

```html
<!DOCTYPE html>
<html lang="en">
<head>
<meta charset="utf-8">
<title>We Are Bright Sparrow</title>
<link href="https://fonts.googleapis.com/css2?family=Montserrat:wght@400;500;600;700;800&family=Satisfy&display=swap" rel="stylesheet">
<style>
:root{
  --ink:#111;
  --muted:#8a8a8a;
  --rule:#cfcfcf;
  --paper:#fff;
  --mist:#f1f1f1;
  --band:#5e5e5e;
  --black:#000;
}
*{margin:0;padding:0;box-sizing:border-box}
html,body{width:1200px;height:5325px;overflow:hidden}
body{position:relative;background:var(--paper);color:var(--ink);font-family:"Montserrat",Arial,sans-serif;font-size:12px}
a{color:inherit;text-decoration:none}
.abs{position:absolute}
.center{text-align:center}
.script{font-family:"Satisfy",cursive;font-weight:400}
.caps{text-transform:uppercase;letter-spacing:.08em;font-weight:700}

/* header */
.site-header{left:0;top:0;width:1200px;height:170px}
.nav-left{left:28px;top:112px;display:flex;gap:34px;align-items:center;font-size:13px}
.nav-right{right:28px;top:112px;display:flex;gap:14px;align-items:center;font-size:13px}
.brand{left:0;top:22px;width:1200px}
.brand-mark{width:30px;height:30px;border:3px solid var(--ink);border-radius:50%;margin:0 auto 12px}
.brand-name{font-size:26px;font-weight:800;letter-spacing:.06em}
.brand-tag{font-size:10px;font-weight:700;letter-spacing:.05em;line-height:15px;margin-top:6px}

/* hero */
.hero-panel{top:185px;width:575px;height:568px;color:#fff}
.hero-armor{left:18px;background:radial-gradient(circle at 55% 30%,#c89a62 0%,#8a5b33 35%,#3a2516 75%,#1e140c 100%)}
.hero-impact{left:607px;background:linear-gradient(160deg,#6a6a66 0%,#3f3b39 40%,#7a3a30 70%,#2b2726 100%)}
.hero-copy{position:absolute;left:0;width:100%;top:250px;text-align:center}
.hero-kicker{font-size:11px;font-weight:600;letter-spacing:.06em}
.hero-title{font-size:32px;font-weight:800;letter-spacing:.04em;margin:10px 0 22px}
.btn-ghost{display:inline-block;border:2px solid #fff;padding:12px 26px;font-size:11px;font-weight:700;letter-spacing:.08em}

/* values */
.values{left:0;top:788px;width:1200px;height:455px;background:var(--mist)}
.values-kicker{top:54px;width:100%;font-size:11px}
.values-title{top:88px;width:100%;font-size:36px}
.value{top:200px;width:300px;text-align:center}
.value svg{display:block;margin:0 auto 36px}
.value p{font-size:12px;line-height:20px;letter-spacing:.04em;font-weight:500;min-height:60px}
.value a{display:inline-block;margin-top:18px;font-size:11px;border-bottom:2px solid var(--ink);padding-bottom:2px}

/* feature blocks */
.photo{display:block}
.card{background:#fff}
.card-row{position:absolute;left:28px;display:flex;gap:28px;align-items:center}
.card-row .thumb{width:180px;height:178px;flex:none}
.card-row h3{font-size:13px;font-weight:700;letter-spacing:.05em;margin-bottom:14px}
.card-row p{font-size:11px;line-height:18px;color:var(--muted);width:300px}
.overlay-label{position:absolute;left:0;width:100%;text-align:center;color:#fff;font-size:14px;font-weight:800;letter-spacing:.06em}

/* armor band */
.armor-band{left:0;top:2485px;width:1200px;height:408px;background:var(--band)}
.armor-photo{left:199px;top:2425px;width:806px;height:345px;background:radial-gradient(ellipse at 55% 55%,#c9955f 0%,#8d5e3a 40%,#4a3526 80%)}
.armor-cta{top:2812px;width:100%;color:#fff;font-size:15px}

/* stories */
.section-title{width:100%;font-size:36px}
.stories-sub{top:3033px;width:100%;font-size:12px;line-height:20px}
.view-all{top:3098px;width:100%;font-size:11px}
.view-all span{border-bottom:2px solid var(--ink);padding-bottom:2px}
.story{top:3170px;width:360px}
.story .photo{height:352px}
.story h4{margin-top:24px;font-size:12px;font-weight:700;letter-spacing:.04em}

/* pictolane strip */
.gallery{left:35px;top:3774px;width:1130px;height:291px;display:flex}
.gallery div{flex:1}

/* power */
.power-title{top:4270px;width:100%;font-size:38px}
.btn-solid-outline{left:486px;top:4349px;width:228px;height:50px;border:2px solid var(--ink);display:flex;align-items:center;justify-content:center;font-size:13px}

/* join */
.join{left:0;top:4494px;width:1200px;height:306px;background:var(--mist)}
.join h2{position:absolute;top:78px;width:100%;text-align:center;font-size:30px;font-weight:800;letter-spacing:.04em}
.join p{position:absolute;top:127px;width:100%;text-align:center;font-size:12px;font-weight:600;letter-spacing:.05em}
.join-form{position:absolute;left:266px;top:185px;width:668px;height:50px;display:flex}
.join-form .field{flex:1;background:#fff;display:flex;align-items:center;padding-left:18px;font-size:10px;color:#aaa}
.join-form .submit{width:175px;background:var(--black);color:#fff;display:flex;align-items:center;justify-content:center;font-size:12px}

/* footer */
.footer-col{top:4862px}
.footer-col h5{font-size:12px;font-weight:800;letter-spacing:.05em;margin-bottom:22px}
.footer-links{display:flex;gap:60px}
.footer-links ul{list-style:none}
.footer-links li{font-size:11px;color:var(--muted);line-height:22px;letter-spacing:.04em}
.touch{top:5124px;width:100%;font-size:11px}
.social{top:5176px;width:100%;display:flex;justify-content:center;gap:34px;font-size:10px;font-weight:700;letter-spacing:.05em}
.social span{display:flex;align-items:center;gap:8px}
.social i{display:block;width:34px;height:34px;border:2px solid var(--ink);border-radius:50%}
.copyright{top:5268px;width:100%;font-size:10px;font-weight:600}
</style>
</head>
<body>

<header class="abs site-header">
  <nav class="abs nav-left caps">
    <svg width="16" height="16" viewBox="0 0 16 16" aria-label="Search"><circle cx="6.5" cy="6.5" r="5" fill="none" stroke="#111" stroke-width="2"/><line x1="10.5" y1="10.5" x2="15" y2="15" stroke="#111" stroke-width="2"/></svg>
    <span style="margin-left:-20px">|</span>
    <a href="#">Shop</a><a href="#">Mission</a><a href="#">Impact</a>
  </nav>
  <div class="abs brand center">
    <div class="brand-mark"></div>
    <div class="brand-name">WE ARE BRIGHT SPARROW</div>
    <div class="brand-tag">AND I WILL CONQUER THE WORLD<br>A GLOBAL EMPOWERMENT MOVEMENT ELEVATING WOMEN, AND THE WORLD</div>
  </div>
  <nav class="abs nav-right caps">
    <a href="#">Account</a><span>|</span>
    <svg width="16" height="20" viewBox="0 0 16 20" aria-label="Bag"><rect x="1" y="6" width="14" height="13" fill="none" stroke="#111" stroke-width="2"/><path d="M5 6V4a3 3 0 0 1 6 0v2" fill="none" stroke="#111" stroke-width="2"/></svg>
    <a href="#">My Bag (0)</a>
  </nav>
</header>

<section class="abs hero-panel hero-armor" role="img" aria-label="Photo of a woman flexing her arms against a sunset sky">
  <div class="hero-copy">
    <div class="hero-kicker">EMBRACE YOUR SUPER POWERS</div>
    <div class="hero-title">OUR ARMOR</div>
    <a class="btn-ghost" href="#">SHOP NOW</a>
  </div>
</section>
<section class="abs hero-panel hero-impact" role="img" aria-label="Photo of a woman working at a bench in a workshop">
  <div class="hero-copy">
    <div class="hero-kicker">IN ELEVATING OURSELVES, WE ELEVATE EACH OTHER</div>
    <div class="hero-title">OUR IMPACT</div>
    <a class="btn-ghost" href="#">LEARN MORE</a>
  </div>
</section>

<section class="abs values">
  <div class="abs values-kicker center caps">At We Are Bright Sparrow we rise together</div>
  <h2 class="abs values-title center script">Empowering Ourselves and Empowering The World</h2>
  <div class="abs value" style="left:66px">
    <svg width="46" height="46" viewBox="0 0 46 46"><path d="M15 4 L4 12 L9 20 L13 17 V42 H33 V17 L37 20 L42 12 L31 4 Q23 11 15 4 Z" fill="none" stroke="#111" stroke-width="2"/></svg>
    <p>WEAR, EMBRACE AND BE<br>EMPOWERED BY OUR ARMOR</p>
    <a class="caps" href="#">Find your armor</a>
  </div>
  <div class="abs value" style="left:450px">
    <svg width="52" height="46" viewBox="0 0 52 46"><path d="M6 8 H38 V28 Q38 40 22 40 Q6 40 6 28 Z" fill="none" stroke="#111" stroke-width="2"/><path d="M38 14 Q48 14 48 22 Q48 28 38 28" fill="none" stroke="#111" stroke-width="2"/></svg>
    <p>PASS IT ON TO A BRIGHT<br>SPARROW YOU KNOW</p>
    <a class="caps" href="#">Share your story</a>
  </div>
  <div class="abs value" style="left:834px">
    <svg width="46" height="46" viewBox="0 0 46 46"><path d="M5 22 L23 6 L41 22 M10 18 V41 H36 V18" fill="none" stroke="#111" stroke-width="2"/></svg>
    <p>SUPPORT INDIVIDUALS &amp; ORGANIZATIONS THAT<br>SUPPORT THE BRIGHT SPARROW MOVEMENT</p>
    <a class="caps" href="#">Learn more</a>
  </div>
</section>

<!-- mission block -->
<div class="abs photo" style="left:103px;top:1285px;width:415px;height:518px;background:linear-gradient(180deg,#8a93a0 0%,#c79a66 45%,#6b4a33 75%,#2d231c 100%)" role="img" aria-label="Photo of a hiker with a backpack on a mountain top at sunrise">
  <div class="overlay-label" style="top:250px">OUR MISSION</div>
</div>
<div class="abs card" style="left:525px;top:1285px;width:572px;height:518px">
  <div class="card-row" style="top:11px">
    <div class="thumb" style="background:linear-gradient(180deg,#d8c2a0,#9b7650)" role="img" aria-label="Photo of a hiker looking over a valley"></div>
    <div><h3>THE MOVEMENT</h3><p>A global circle of women lifting one another, sharing strength and turning courage into lasting change every day.</p></div>
  </div>
  <div class="card-row" style="top:277px">
    <div class="thumb" style="background:linear-gradient(180deg,#a9987e,#4f4032)" role="img" aria-label="Photo of a woman resting on a rocky summit"></div>
    <div><h3>THE MANTRA</h3><p>We speak it daily: I am strong, I am seen, and I will conquer the world with kindness.</p></div>
  </div>
</div>

<!-- communities block -->
<div class="abs card" style="left:103px;top:1842px;width:586px;height:518px">
  <div class="card-row" style="top:70px;left:40px;gap:22px">
    <div class="thumb" style="width:180px;height:180px;background:linear-gradient(180deg,#d9b4b8,#9a7d84)" role="img" aria-label="Photo of three smiling women outdoors"></div>
    <div><h3>OUR COMMUNITIES</h3><p>Local groups meet, mentor and build together, creating safe places where every woman can grow and lead with heart.</p></div>
  </div>
  <div class="card-row" style="top:272px;left:40px;gap:22px">
    <div class="thumb" style="width:180px;height:180px;background:linear-gradient(180deg,#6f7d96,#3c4458)" role="img" aria-label="Photo of an older woman smiling"></div>
    <div><h3>NOMINATE</h3><p>Know a woman who lifts others? Share her name so we can celebrate her story and pass the power on.</p></div>
  </div>
</div>
<div class="abs photo" style="left:689px;top:1842px;width:408px;height:518px;background:linear-gradient(180deg,#b6a9a2 0%,#8e7668 50%,#7a7f8c 100%)" role="img" aria-label="Photo of a group of women joining hands in the centre">
  <div class="overlay-label" style="top:250px">OUR IMPACT</div>
</div>

<!-- armor band -->
<div class="abs armor-band"></div>
<div class="abs armor-photo" role="img" aria-label="Close-up photo of a hand wearing a ring and bracelet"></div>
<div class="abs armor-cta center caps">Shop our armor</div>

<!-- stories -->
<h2 class="abs section-title center script" style="top:2958px">Bright Sparrow Stories</h2>
<div class="abs stories-sub center caps">Read about real Bright Sparrows, how they are empowering<br>themselves and healing the world</div>
<div class="abs view-all center caps"><span>View all</span></div>
<article class="abs story" style="left:35px">
  <div class="photo" style="background:linear-gradient(180deg,#c9a27a,#7b8a9a)" role="img" aria-label="Portrait photo of a woman outdoors"></div>
  <h4>MY BRIGHT SPARROW STORY</h4>
</article>
<article class="abs story" style="left:422px">
  <div class="photo" style="background:linear-gradient(180deg,#d08f55,#2e3c5e)" role="img" aria-label="Portrait photo of a businesswoman at a laptop"></div>
  <h4>I CAME AND I CONQUERED</h4>
</article>
<article class="abs story" style="left:809px">
  <div class="photo" style="background:linear-gradient(180deg,#c6c8cc,#8f8479)" role="img" aria-label="Portrait photo of a smiling woman in a striped top"></div>
  <h4>THE POWER OF LOVE</h4>
</article>

<!-- pictolane -->
<h2 class="abs section-title center script" style="top:3656px">Shop Our Pictolane</h2>
<div class="abs center" style="top:3726px;width:100%;font-size:10px">@wearebrightsparrow</div>
<div class="abs gallery">
  <div style="background:linear-gradient(180deg,#7a7464,#a06a4a)" role="img" aria-label="Photo of a woman sitting outdoors"></div>
  <div style="background:linear-gradient(180deg,#8f8779,#3d352c)" role="img" aria-label="Photo of a woman on a rock by the water"></div>
  <div style="background:linear-gradient(180deg,#c6c0b4,#8a7f6a)" role="img" aria-label="Photo of a woman meditating by the sea"></div>
  <div style="background:radial-gradient(circle at 50% 40%,#f1b35b,#c4632e 50%,#3a2518)" role="img" aria-label="Photo of a woman climbing at sunset"></div>
</div>

<!-- power -->
<h2 class="abs power-title center script">It's Time To Step Into Your Power</h2>
<a class="abs btn-solid-outline caps" href="#">Buy your armor</a>

<!-- join -->
<section class="abs join">
  <h2>JOIN THE MOVEMENT</h2>
  <p>KEEP CONNECTED, STAY EMPOWERED</p>
  <div class="join-form">
    <div class="field">Enter Your E-Mail Address</div>
    <div class="submit caps">Sign me up !</div>
  </div>
</section>

<!-- footer -->
<footer>
  <div class="abs footer-col" style="left:35px">
    <h5>SHOP</h5>
    <div class="footer-links">
      <ul><li>ALL JEWELRY</li><li>NECKLACES</li><li>BRACELETS</li><li>EARRINGS</li></ul>
      <ul><li>KEYCHAINS</li><li>BEST SELLERS</li><li>GIFTS UNDER $50</li><li>SALE</li></ul>
    </div>
  </div>
  <div class="abs footer-col" style="left:422px">
    <h5>MISSION</h5>
    <div class="footer-links">
      <ul><li>SHOP</li><li>MISSION</li><li>ABOUT US</li><li>OUR IMPACT</li><li>PRESS</li><li>CAREERS</li></ul>
      <ul><li>SHARE YOUR STORY</li><li>PAY IT FORWARD STORY</li><li>THE EXCHANGE PROJECT</li><li>SHOP OUR PICTOLANE</li></ul>
    </div>
  </div>
  <div class="abs footer-col" style="left:813px">
    <h5>CUSTOMER CARE</h5>
    <div class="footer-links">
      <ul><li>YOUR ACCOUNT</li><li>CONTACT/FAQ</li><li>STORE LOCATOR</li></ul>
      <ul><li>RETURNS</li><li>JEWELRY CARE</li></ul>
    </div>
  </div>
  <div class="abs touch center caps">Keep in touch</div>
  <div class="abs social">
    <span><i></i>PAGEWAVE</span>
    <span><i></i>PICTOLANE</span>
  </div>
  <div class="abs copyright center">© Copyright We Are Bright Sparrow 2017</div>
</footer>

</body>
</html>
```